A Vegan Nutritional Supplement (one Product) website

I am looking for an experienced Web designer to build a One Product website for a Nutritional Supplement that is 100% vegan. The emphasis would be on both the Quality and Quantity of the ingredients and their benefits. It contains Essential Vitamins, Minerals, and a proprietary blend of 42 Fruits and Vegetables. I welcome color suggestions as long as it includes Green (vegan) and White.. The final design should communicate to the buyer: Quality, Healthy, Safety (Natural vegan ingredients), Natural energy, well being. The product includes benefits for 3 vital elements of optimal health: Immune Health, Heart Health, and Brain Health

Industry/Entity Type

Health and Wellness - Nutritional Supplements

Number of Pages Required

4 page

Other font styles liked:
• I Welcome your creativity

Colors
59FF00
82FF00
B8FF75
E3FFCB
F4FFEA

Requirements
Must have
• Options to purchase : One product ($34.95); 2 products ($31.45 each - 10% discount), or 3 Products ($27.95 each - 20% discount)
Nice to have
• Focus on the Benefits of having all these Ingredients - Nutrients in one bottle - Essential Vitamins, Minerals, and proprietary blend of 42 Fruits and Vegetables.

```html
<!DOCTYPE html>
<html lang="en">
<head>
<meta charset="utf-8">
<title>Leafora – Verde Vigor</title>
<link rel="stylesheet" href="https://fonts.googleapis.com/css2?family=Libre+Baskerville:wght@400;700&family=Mulish:wght@400;600;700;800&display=swap">
<style>
:root{
  --green:#59FF00;
  --lime:#82FF00;
  --soft:#B8FF75;
  --mint:#E3FFCB;
  --page:#EEFFE2;
  --ink:#1b1b1b;
  --text:#333;
  --deep:#1f6b2a;
}
*{box-sizing:border-box;margin:0;padding:0}
html,body{width:1200px;height:4926px;overflow:hidden}
body{background:var(--page);font-family:'Mulish',sans-serif;color:var(--text);position:relative}
.abs{position:absolute}
.serif{font-family:'Libre Baskerville',serif}
.btn{position:absolute;background:var(--green);color:var(--ink);font-weight:800;font-size:14px;letter-spacing:.3px;display:flex;align-items:center;justify-content:center;text-transform:uppercase}
.rule{position:absolute;height:3px;background:var(--green);width:46px}
.photo{position:absolute}
.brand{font-family:'Libre Baskerville',serif;font-weight:700;color:var(--deep);font-size:30px;display:flex;align-items:center;gap:8px}
.brand i{display:block;width:14px;height:14px;border-radius:50%;background:var(--lime)}

.header{position:absolute;left:0;top:0;width:1200px;height:78px;background:var(--page);border-bottom:1px solid #dfeed3}
.nav{position:absolute;top:26px;left:476px;display:flex;font-size:13px;font-weight:600;color:var(--ink)}
.nav span{padding:4px 10px;margin-right:14px}
.nav .active{background:var(--green)}
.cart{position:absolute;left:1016px;top:28px;font-size:12px;font-weight:600;display:flex;gap:6px;align-items:center;color:var(--ink)}

.hero{position:absolute;left:0;top:78px;width:1200px;height:543px;background:linear-gradient(120deg,#6b8a2a,#8a3a2e 35%,#c5a43a 60%,#4f7a22 85%,#7a2f3a)}
.hero-shade{position:absolute;inset:0;background:linear-gradient(90deg,rgba(0,0,0,.45),rgba(0,0,0,.2) 60%,rgba(0,0,0,.1))}
.hero-tag{left:176px;top:147px;background:#1f8a1f;color:#fff;font-size:22px;padding:5px 10px}
.hero-title{left:170px;top:200px;color:#fff;font-size:56px;font-weight:700}
.hero-sub{left:174px;top:278px;color:#fff;font-size:18px;line-height:32px;font-weight:700;width:440px}
.arrow{position:absolute;top:255px;width:36px;height:36px;background:#e9e9e9;display:flex;align-items:center;justify-content:center}

.about-tag{left:634px;top:730px;background:var(--green);color:var(--ink);font-size:20px;padding:7px 12px}
.about-head{left:634px;top:790px;font-size:18px;line-height:30px;color:var(--ink);width:360px}
.about-copy{left:634px;top:906px;width:440px;font-size:13px;line-height:19.5px;color:var(--text)}
.about-copy p{margin-bottom:19px}

.sec-title{position:absolute;width:1200px;text-align:center;font-family:'Libre Baskerville',serif;font-size:19px;font-weight:700;color:var(--ink)}

.card{position:absolute;top:1364px;width:304px;height:500px;background:#fff}
.card .pic{position:absolute;left:0;top:0;width:304px;height:180px;background:linear-gradient(135deg,#7a9a3a,#b14a3a 45%,#d9b54a 75%,#5c8a2a)}
.card .bottle{position:absolute;top:40px;width:124px;height:270px;border-radius:30px 30px 14px 14px;background:linear-gradient(180deg,#f2f2f2 0 18%,#2f7a2f 18% 86%,#ececec 86%)}
.ribbon{position:absolute;left:-4px;top:-4px;width:90px;height:90px;overflow:hidden}
.ribbon span{position:absolute;left:-26px;top:26px;width:140px;transform:rotate(-45deg);background:var(--green);font-size:11px;text-align:center;padding:3px 0;color:var(--ink)}
.card .name{position:absolute;top:358px;width:100%;text-align:center;font-family:'Libre Baskerville',serif;font-size:17px;color:var(--ink)}
.card .price{position:absolute;top:392px;width:100%;text-align:center;font-family:'Libre Baskerville',serif;font-size:24px;color:var(--ink)}
.card .btn{left:94px;top:434px;width:116px;height:37px}

.benefit{position:absolute;width:200px;text-align:center;font-size:12.5px;line-height:20px;color:var(--ink)}
.benefit .ring{width:86px;height:86px;margin:0 auto 14px;border:2px solid #a7ee85;border-radius:50%;display:flex;align-items:center;justify-content:center;background:var(--page)}

.why-top{left:0;top:2436px;width:965px;height:168px;background:var(--green)}
.why-left{left:0;top:2603px;width:520px;height:384px;background:var(--green)}
.why-title{left:134px;top:2482px;font-size:26px;color:var(--ink)}
.why-copy{left:430px;top:2482px;width:480px;font-size:13px;line-height:22px;color:var(--ink)}
.feature{position:absolute;width:200px;text-align:center;font-size:13px;line-height:17px;color:var(--ink);text-transform:uppercase}
.feature svg{display:block;margin:0 auto 10px}

.quote{position:absolute;top:3210px;width:298px;height:320px;border:1.5px solid #b2ec90;border-top:none}
.quote .mark{position:absolute;font-family:'Libre Baskerville',serif;font-size:40px;color:var(--green);font-weight:700;line-height:1}
.quote p{position:absolute;left:38px;top:32px;width:234px;font-size:12.5px;line-height:19.3px;color:var(--text)}
.quote b{position:absolute;left:38px;top:266px;font-size:12.5px;color:var(--ink)}
.dot{position:absolute;top:3571px;width:9px;height:9px;border-radius:50%;background:#bbb}

.nutri{left:0;top:3637px;width:1200px;height:367px;background:var(--mint);overflow:hidden}
.nutri-title{left:0;top:3700px;width:1280px;text-align:center;font-size:33px;color:var(--ink)}
.nutri-tag{left:452px;top:3757px;width:378px;height:46px;background:var(--green);font-family:'Libre Baskerville',serif;font-size:20px;font-weight:700;color:var(--ink);display:flex;align-items:center;justify-content:center}
.nutri-copy{left:440px;top:3830px;width:400px;text-align:center;font-size:13px;line-height:20px;color:var(--ink)}

.faq{position:absolute;left:200px;width:841px;height:56px;border-bottom:1.5px solid #555;font-size:18px;color:var(--ink);display:flex;align-items:center;justify-content:space-between;padding:0 0 0 2px}

.footer{left:0;top:4583px;width:1200px;height:343px;background:var(--mint)}
.fhead{position:absolute;font-size:12.5px;font-weight:800;color:var(--ink);letter-spacing:.3px}
.fitem{position:absolute;font-size:11.5px;line-height:16px;color:var(--ink)}
.ficon{position:absolute;width:22px;height:22px;border-radius:50%;background:var(--ink)}
</style>
</head>
<body>

<header class="header">
  <div class="brand abs" style="left:134px;top:20px"><i></i>Leafora</div>
  <nav class="nav">
    <span class="active">Home</span><span>About Us</span><span>Services</span><span>Products</span><span>Blog</span><span>Contact Us</span>
  </nav>
  <div class="cart">Cart
    <svg width="24" height="22" viewBox="0 0 24 22" fill="none" stroke="#1b1b1b" stroke-width="1.8"><path d="M1 2h4l3 12h12l3-9H7"/><circle cx="10" cy="19" r="1.6"/><circle cx="19" cy="19" r="1.6"/></svg>
  </div>
</header>

<section class="hero" role="img" aria-label="Colourful heap of fresh fruits and vegetables with a bottle of Verde Vigor supplement tablets">
  <div class="hero-shade"></div>
  <div class="photo" role="img" aria-label="Verde Vigor supplement bottle" style="left:672px;top:38px;width:294px;height:505px;border-radius:60px 60px 20px 20px;background:linear-gradient(180deg,#f3f3f3 0 22%,#2e7a30 22% 90%,#e6e6e6 90%)"></div>
  <div class="abs hero-tag">100% vegan</div>
  <h1 class="abs serif hero-title">Verde Vigor</h1>
  <p class="abs serif hero-sub">Essential Vitamins &amp; Minerals with 42 Fruits &amp; Vegetables Proprietary Blend</p>
  <div class="btn" style="left:174px;top:363px;width:122px;height:37px">Shop Now</div>
  <div class="arrow" style="left:0"><svg width="12" height="14" viewBox="0 0 12 14"><path d="M9 1 3 7l6 6" stroke="#222" stroke-width="2" fill="none"/></svg></div>
  <div class="arrow" style="left:1164px"><svg width="12" height="14" viewBox="0 0 12 14"><path d="M3 1l6 6-6 6" stroke="#222" stroke-width="2" fill="none"/></svg></div>
</section>

<section class="about">
  <div class="photo" role="img" aria-label="Smiling woman in a kitchen holding a Verde Vigor bottle and taking a tablet" style="left:130px;top:697px;width:455px;height:526px;background:linear-gradient(160deg,#f1f1ef,#d9d9d4 55%,#b8b6ad)"></div>
  <div class="abs serif about-tag">Verde Vigor</div>
  <h2 class="abs serif about-head">A Powerful Supplement for Getting Optimal Health</h2>
  <div class="rule" style="left:634px;top:869px;width:70px"></div>
  <div class="abs about-copy">
    <p>When healthy food is a nuisance, a weak immune system, the risk of chronic and mental illnesses in old age is quite common. According to one report of a national health agency, the majority of the US population is not able to get the necessary nutrients by a healthy diet alone1. Therefore, you must take supplements to meet your nutrient needs.</p>
    <p>We present with you Verde Vigor, a miracle supplement, a specific proprietary blend derived from a large number of herbs, fruits, and vegetables, and a lot of regular expected vitamins and minerals, for the need of optimal health.</p>
    <p>You can eat a maximum of two or three fruits and vegetables in one day, but by taking this supplement, you can get the nutrients of 42 different fruits and vegetables along with other multivitamins. Let's review some health benefits of taking Verde Vigor</p>
  </div>
</section>

<section class="shop">
  <h2 class="sec-title" style="top:1282px">Shop</h2>
  <div class="rule" style="left:577px;top:1318px"></div>

  <div class="card" style="left:130px">
    <div class="pic" role="img" aria-label="Fresh fruits and vegetables background"></div>
    <div class="bottle" role="img" aria-label="One Verde Vigor bottle" style="left:90px"></div>
    <div class="name">One Product</div><div class="price">$34.95</div><div class="btn">Shop Now</div>
  </div>
  <div class="card" style="left:449px">
    <div class="pic" role="img" aria-label="Fresh fruits and vegetables background"></div>
    <div class="bottle" role="img" aria-label="Verde Vigor bottle" style="left:36px"></div>
    <div class="bottle" role="img" aria-label="Verde Vigor bottle" style="left:142px"></div>
    <div class="ribbon"><span>10% Discount</span></div>
    <div class="name">2 Products</div><div class="price">$31.45</div><div class="btn">Shop Now</div>
  </div>
  <div class="card" style="left:768px">
    <div class="pic" role="img" aria-label="Fresh fruits and vegetables background"></div>
    <div class="bottle" role="img" aria-label="Verde Vigor bottle" style="left:20px;width:100px;top:70px;height:230px"></div>
    <div class="bottle" role="img" aria-label="Verde Vigor bottle" style="left:184px;width:100px;top:70px;height:230px"></div>
    <div class="bottle" role="img" aria-label="Verde Vigor bottle" style="left:102px;width:100px;top:70px;height:230px"></div>
    <div class="ribbon"><span>20% Discount</span></div>
    <div class="name">3 Products</div><div class="price">$27.95</div><div class="btn">Shop Now</div>
  </div>
</section>

<section class="benefits">
  <h2 class="sec-title" style="top:1920px">Benefits</h2>
  <div class="rule" style="left:580px;top:1956px"></div>

  <div class="benefit" style="left:87px;top:2019px"><div class="ring"><svg width="40" height="40" viewBox="0 0 40 40" fill="none" stroke="#222" stroke-width="1.6"><ellipse cx="14" cy="14" rx="6" ry="4"/><ellipse cx="27" cy="20" rx="6" ry="4"/><ellipse cx="15" cy="28" rx="6" ry="4"/></svg></div>Formation of Red<br>Blood Cells</div>
  <div class="benefit" style="left:294px;top:2019px"><div class="ring"><svg width="44" height="44" viewBox="0 0 44 44" fill="none" stroke="#222" stroke-width="1.6"><circle cx="22" cy="22" r="7"/><path d="M22 4v8M22 32v8M4 22h8M32 22h8M9 9l6 6M29 29l6 6M35 9l-6 6M9 35l6-6"/></svg></div>Reduce Cancer and<br>Heart Disease Risk</div>
  <div class="benefit" style="left:500px;top:2019px"><div class="ring"><svg width="40" height="40" viewBox="0 0 40 40" fill="none" stroke="#222" stroke-width="1.6"><path d="M12 34v-8a12 12 0 1 1 16 0h-4v8"/><circle cx="20" cy="16" r="4"/></svg></div>Improve<br>Mental Health</div>
  <div class="benefit" style="left:687px;top:2019px"><div class="ring"><svg width="36" height="40" viewBox="0 0 36 40" fill="none" stroke="#222" stroke-width="1.6"><rect x="7" y="6" width="22" height="30" rx="3"/><rect x="11" y="11" width="14" height="8"/><circle cx="18" cy="28" r="3"/></svg></div>Manage Blood<br>Sugar Levels</div>
  <div class="benefit" style="left:890px;top:2019px"><div class="ring"><svg width="44" height="44" viewBox="0 0 44 44" fill="none" stroke="#222" stroke-width="1.6"><path d="M22 6a16 16 0 0 1 15 12M37 26a16 16 0 0 1-15 12M7 26A16 16 0 0 1 11 10"/><path d="M22 30s-7-4-7-9a4 4 0 0 1 7-2 4 4 0 0 1 7 2c0 5-7 9-7 9z"/></svg></div>Control Blood Pressure<br>and Improve Blood Flow</div>

  <div class="benefit" style="left:87px;top:2210px"><div class="ring"><svg width="36" height="40" viewBox="0 0 36 40" fill="none" stroke="#222" stroke-width="1.6"><path d="M9 6c5-2 8 1 9 1s4-3 9-1c5 3 3 12 1 16-2 5-2 13-5 13s-2-9-5-9-2 9-5 9-3-8-5-13C6 18 4 9 9 6z"/></svg></div>Support Bone<br>and Teeth Health</div>
  <div class="benefit" style="left:294px;top:2210px"><div class="ring"><svg width="40" height="40" viewBox="0 0 40 40" fill="none" stroke="#222" stroke-width="1.6"><path d="M20 8v12L8 32M20 20l12 12"/><circle cx="20" cy="7" r="3" fill="#222"/><circle cx="20" cy="20" r="3" fill="#222"/><circle cx="8" cy="32" r="3" fill="#222"/><circle cx="32" cy="32" r="3" fill="#222"/></svg></div>Increase Energy (ATP)<br>and Regulate Metabolism</div>
  <div class="benefit" style="left:500px;top:2210px"><div class="ring"><svg width="40" height="30" viewBox="0 0 40 30" fill="none" stroke="#222" stroke-width="1.8"><path d="M2 15s7-11 18-11 18 11 18 11-7 11-18 11S2 15 2 15z"/><circle cx="20" cy="15" r="5"/></svg></div>Support Vision<br>and Eye Health</div>
  <div class="benefit" style="left:687px;top:2210px"><div class="ring"><svg width="40" height="40" viewBox="0 0 40 40" fill="none" stroke="#222" stroke-width="1.6"><path d="M12 4c0 8 8 8 8 16s-8 8-8 16M28 4c0 8-8 8-8 16s8 8 8 16"/></svg></div>Improve Digestion<br>and Weight Loss</div>
  <div class="benefit" style="left:890px;top:2210px"><div class="ring"><svg width="40" height="40" viewBox="0 0 40 40" fill="none" stroke="#222" stroke-width="1.6"><circle cx="20" cy="15" r="8"/><path d="M6 38c2-8 8-12 14-12s12 4 14 12"/></svg></div>Skin, Hair, And<br>Nails Health</div>
</section>

<section class="why">
  <div class="abs why-top"></div>
  <div class="abs why-left"></div>
  <h2 class="abs serif why-title">Why Choose Us</h2>
  <div class="rule" style="left:134px;top:2531px;width:48px;background:#1b1b1b;height:2px"></div>
  <p class="abs why-copy">There are many variations of passages of Lorem Ipsum available, but the majority have suffered alteration in some form, by injected humour, or randomised words which don't look even slightly believable. If you are going to use a passage of Lorem Ipsum, you need to be sure there</p>

  <div class="feature" style="left:103px;top:2614px"><svg width="34" height="38" viewBox="0 0 34 38" fill="none" stroke="#111" stroke-width="1.8"><rect x="7" y="2" width="20" height="6"/><rect x="4" y="8" width="26" height="28" rx="3"/><path d="M11 20h12M17 14v12"/></svg>Nutrients in<br>one bottle</div>
  <div class="feature" style="left:301px;top:2614px"><svg width="40" height="38" viewBox="0 0 40 38" fill="none" stroke="#111" stroke-width="1.6"><circle cx="13" cy="14" r="6"/><circle cx="27" cy="14" r="6"/><circle cx="20" cy="27" r="6"/><path d="M4 4l4 4M36 4l-4 4M20 34v3"/></svg>Essential<br>vitamins</div>
  <div class="feature" style="left:103px;top:2733px"><svg width="34" height="36" viewBox="0 0 34 36" fill="none" stroke="#111" stroke-width="1.8"><path d="M17 2l13 5v10c0 8-6 14-13 17C10 31 4 25 4 17V7z"/><path d="M11 18l4 4 8-8"/></svg>Trusted<br>ingredients</div>
  <div class="feature" style="left:301px;top:2733px"><svg width="34" height="36" viewBox="0 0 34 36" fill="none" stroke="#111" stroke-width="1.8"><path d="M6 32C6 14 18 4 30 4c0 14-8 24-22 24M6 32l14-16"/></svg>Regenerative<br>practices</div>
  <div class="feature" style="left:103px;top:2850px"><svg width="30" height="36" viewBox="0 0 30 36" fill="none" stroke="#111" stroke-width="1.8"><path d="M15 2C9 12 4 17 4 23a11 11 0 0 0 22 0c0-6-5-11-11-21z"/><circle cx="12" cy="24" r="3"/><circle cx="19" cy="19" r="2"/></svg>Minerals</div>
  <div class="feature" style="left:301px;top:2850px"><svg width="40" height="36" viewBox="0 0 40 36" fill="none" stroke="#111" stroke-width="1.6"><circle cx="13" cy="24" r="9"/><circle cx="28" cy="23" r="8"/><path d="M13 15c0-5 3-9 7-10M26 15l2-8"/></svg>Proprietary blend<br>of 42 fruits and<br>vegetables</div>

  <div class="photo" role="img" aria-label="Cheerful woman on a sofa holding a Verde Vigor bottle and a capsule, with a gift box of supplements on the table" style="left:522px;top:2603px;width:678px;height:456px;background:linear-gradient(150deg,#d8dad6,#9a9d97 50%,#4c4e4b)"></div>
</section>

<section class="testimonials">
  <h2 class="sec-title" style="top:3118px">Testimonials</h2>
  <div class="rule" style="left:577px;top:3154px"></div>

  <div class="quote" style="left:130px"><span class="mark" style="left:0;top:-6px">&ldquo;</span><p>There are many variations of passages of Lorem Ipsum available, but the majority have suffered alteration in some form, by injected humour, or randomised words which don't look even slightly believable. If you are going to use a passage of Lorem Ipsum, you need to be sure there isn't anything embarrassing hidden in the middle of text</p><b>Daniel</b><span class="mark" style="right:-4px;bottom:-18px">&rdquo;</span></div>
  <div class="quote" style="left:453px"><span class="mark" style="left:0;top:-6px">&ldquo;</span><p>There are many variations of passages of Lorem Ipsum available, but the majority have suffered alteration in some form, by injected humour, or randomised words which don't look even slightly believable. If you are going to use a passage of Lorem Ipsum, you need to be sure there isn't anything embarrassing hidden in the middle of text</p><b>Daniel</b><span class="mark" style="right:-4px;bottom:-18px">&rdquo;</span></div>
  <div class="quote" style="left:772px"><span class="mark" style="left:0;top:-6px">&ldquo;</span><p>There are many variations of passages of Lorem Ipsum available, but the majority have suffered alteration in some form, by injected humour, or randomised words which don't look even slightly believable. If you are going to use a passage of Lorem Ipsum, you need to be sure there isn't anything embarrassing hidden in the middle of text</p><b>Daniel</b><span class="mark" style="right:-4px;bottom:-18px">&rdquo;</span></div>

  <span class="dot" style="left:564px"></span><span class="dot" style="left:580px"></span><span class="dot" style="left:597px;background:var(--green)"></span><span class="dot" style="left:614px"></span><span class="dot" style="left:631px"></span>
</section>

<section class="abs nutri">
  <div class="photo" role="img" aria-label="Tilted Verde Vigor supplement bottle" style="left:60px;top:30px;width:320px;height:337px;border-radius:60px 60px 20px 20px;transform:rotate(16deg);background:linear-gradient(180deg,#f3f3f3 0 24%,#2e7a30 24% 92%,#e6e6e6 92%)"></div>
  <div class="photo" role="img" aria-label="Wooden spoon holding green vegan capsules" style="left:940px;top:30px;width:120px;height:337px;border-radius:60px 60px 20px 20px;background:linear-gradient(180deg,#8bbf3a 0 40%,#a8743c 40%)"></div>
</section>
<h2 class="abs serif nutri-title">Nutritional Supplement</h2>
<div class="abs nutri-tag">Verde Vigor that is 100% vegan.</div>
<p class="abs nutri-copy">There are many variations of passages of Lorem Ipsum available, but the majority have suffered alteration in some form, by injected humour, or randomised words which don't look.</p>
<div class="btn" style="left:580px;top:3914px;width:116px;height:34px">Shop Now</div>

<section class="faqs">
  <h2 class="sec-title" style="top:4055px">You got Questions. We got Answers.</h2>
  <div class="rule" style="left:580px;top:4102px"></div>
  <div class="faq" style="top:4150px">Do I ned a doctor's Approval?<svg width="16" height="10" viewBox="0 0 16 10"><path d="M2 2l6 6 6-6" stroke="#222" stroke-width="1.8" fill="none"/></svg></div>
  <div class="faq" style="top:4206px">Are They Natural?<svg width="16" height="10" viewBox="0 0 16 10"><path d="M2 2l6 6 6-6" stroke="#222" stroke-width="1.8" fill="none"/></svg></div>
  <div class="faq" style="top:4262px">Are there any side effects?<svg width="16" height="10" viewBox="0 0 16 10"><path d="M2 2l6 6 6-6" stroke="#222" stroke-width="1.8" fill="none"/></svg></div>
  <div class="faq" style="top:4318px">Is there any proof they work?<svg width="16" height="10" viewBox="0 0 16 10"><path d="M2 2l6 6 6-6" stroke="#222" stroke-width="1.8" fill="none"/></svg></div>
  <div class="faq" style="top:4374px">Why should i take supplements?<svg width="16" height="10" viewBox="0 0 16 10"><path d="M2 2l6 6 6-6" stroke="#222" stroke-width="1.8" fill="none"/></svg></div>
  <div class="faq" style="top:4430px">How are your ingredients unique?<svg width="16" height="10" viewBox="0 0 16 10"><path d="M2 2l6 6 6-6" stroke="#222" stroke-width="1.8" fill="none"/></svg></div>
  <div class="faq" style="top:4486px;border-bottom:none">How are your capsules unique?<svg width="16" height="10" viewBox="0 0 16 10"><path d="M2 2l6 6 6-6" stroke="#222" stroke-width="1.8" fill="none"/></svg></div>
</section>

<footer class="abs footer">
  <div class="brand abs" style="left:138px;top:120px;font-size:40px"><i style="width:18px;height:18px"></i>Leafora</div>

  <div class="fhead" style="left:397px;top:40px">CONTACT US</div>
  <span class="ficon" style="left:397px;top:86px"></span>
  <div class="fitem" style="left:430px;top:82px">Unit 4, Level 2,<br>210-214 Meadow Lane, Greenfield GV 4820.</div>
  <span class="ficon" style="left:397px;top:145px"></span>
  <div class="fitem" style="left:430px;top:141px">Call Us<br>+1 555 014 2290</div>
  <span class="ficon" style="left:397px;top:200px"></span>
  <div class="fitem" style="left:430px;top:196px">E mail Us<br>hello@leaforaverdevigor.com</div>

  <div class="fhead" style="left:770px;top:40px">MENU</div>
  <div class="fitem" style="left:770px;top:74px;line-height:24.5px">HOME<br>ABOUT US<br>SERVICES<br>PRODUCTS<br>BLOG<br>CONTACT US</div>

  <div class="fhead" style="left:967px;top:40px">FOLLOW US</div>
  <span class="ficon" style="left:965px;top:80px"></span>
  <div class="fitem" style="left:1000px;top:76px">Like us on<br>SPROUTBOOK</div>
  <span class="ficon" style="left:965px;top:130px"></span>
  <div class="fitem" style="left:1000px;top:126px">Follow us on<br>CHIRPLY</div>
  <span class="ficon" style="left:965px;top:180px"></span>
  <div class="fitem" style="left:1000px;top:176px">Follow us on<br>WORKGROVE</div>

  <div class="abs" style="left:130px;top:254px;width:940px;height:1px;background:#777"></div>
  <div class="fitem" style="left:0;top:292px;width:1200px;text-align:center;font-size:11px">Copyright © 2022 All Rights Reserved</div>
</footer>

</body>
</html>
```